Business card for law firm

Need business card for new law firm. Think confident, authoritative, conservative, but not stuffy or old-fashioned.

Contact Information for Business Card

Content for card - logo (uploaded), plus the following:

Paul Whitcombe (larger font)
Managing Partner (larger font, but not as large as name)
Level 9, 7 Ferris Lane
Sydney NSW 2000
Main Tel 02 9364 2710
Direct Tel 02 8472 3159
Email paul@qvlegal.com.au
www.qvlegal.com.au

Letterhead design should include logo plus:
Level 9, 7 Ferris Lane
Sydney NSW 2000
Tel 02 8472 3159
www.qvlegal.com.au

```html
<!DOCTYPE html>
<html lang="en">
<head>
<meta charset="utf-8">
<title>Quayvale Legal – Business Card</title>
<link rel="stylesheet" href="https://fonts.googleapis.com/css2?family=Jost:wght@400;500;600&display=swap">
<style>
  :root {
    --navy: #0f1f5e;
    --white: #ffffff;
    --paper: #fdfdfd;
    --muted: #b8c3e6;
    --divider: #5d6066;
    --backdrop: #47494d;
  }
  * { box-sizing: border-box; margin: 0; padding: 0; }
  html, body { width: 1200px; height: 1000px; overflow: hidden; }
  body {
    background: var(--backdrop);
    font-family: "Jost", sans-serif;
    position: relative;
  }
  .card {
    position: absolute;
    left: 290px;
    width: 620px;
    height: 378px;
    border-radius: 22px;
    overflow: hidden;
  }
  .card--front { top: 80px; background: var(--navy); }
  .card--back { top: 520px; display: flex; background: var(--navy); }

  .brand-name {
    display: flex;
    align-items: center;
    justify-content: center;
    gap: 14px;
    font-family: "Jost", sans-serif;
    font-weight: 500;
    line-height: 1;
    white-space: nowrap;
  }
  .brand-name__square { flex: none; }

  .card--front .brand-name {
    position: absolute; left: 0; right: 0; top: 150px;
    color: var(--white); font-size: 46px;
  }
  .card--front .brand-name__square { width: 40px; height: 40px; background: var(--white); }
  .front__url {
    position: absolute; left: 0; right: 0; top: 290px;
    text-align: center; color: var(--white);
    font-size: 18px; letter-spacing: 1px;
  }

  .back__brand {
    width: 300px; background: var(--paper);
    display: flex; align-items: center; justify-content: center;
  }
  .back__brand .brand-name { color: var(--navy); font-size: 30px; gap: 10px; }
  .back__brand .brand-name__square { width: 28px; height: 28px; background: var(--navy); }
  .back__divider { width: 7px; background: var(--divider); }

  .contact {
    flex: 1; color: var(--white);
    padding: 58px 0 0 32px;
    font-size: 16px; line-height: 1.3;
  }
  .contact__name { font-weight: 600; font-size: 23px; text-transform: uppercase; letter-spacing: 0.3px; }
  .contact__role { color: var(--muted); font-size: 18px; margin-bottom: 16px; }
  .contact__address { margin-bottom: 14px; }
  .contact__line { display: flex; align-items: center; gap: 8px; }
  .contact__label { font-weight: 600; }
  .contact__icon { width: 14px; height: 14px; flex: none; }
</style>
</head>
<body>
  <section class="card card--front">
    <div class="brand-name">
      <span class="brand-name__square"></span>
      <span>Quayvale Legal</span>
    </div>
    <p class="front__url">www.qvlegal.com.au</p>
  </section>

  <section class="card card--back">
    <div class="back__brand">
      <div class="brand-name">
        <span class="brand-name__square"></span>
        <span>Quayvale Legal</span>
      </div>
    </div>
    <div class="back__divider"></div>
    <div class="contact">
      <p class="contact__name">Paul Whitcombe</p>
      <p class="contact__role">Managing Partner</p>
      <p class="contact__address">Level 9, 7 Ferris Lane<br>Sydney NSW 2000</p>
      <p class="contact__line"><span class="contact__label">Main Tel</span> 02 9364 2710</p>
      <p class="contact__line"><span class="contact__label">Direct Tel</span> 02 8472 3159</p>
      <p class="contact__line">
        <svg class="contact__icon" viewBox="0 0 14 14" aria-hidden="true"><rect x="1" y="3" width="12" height="8" fill="none" stroke="#fff" stroke-width="1.3"/><path d="M1 3 L7 8 L13 3" fill="none" stroke="#fff" stroke-width="1.3"/></svg>
        paul@qvlegal.com.au
      </p>
      <p class="contact__line">
        <svg class="contact__icon" viewBox="0 0 14 14" aria-hidden="true"><circle cx="7" cy="7" r="6" fill="none" stroke="#fff" stroke-width="1.2"/><ellipse cx="7" cy="7" rx="2.6" ry="6" fill="none" stroke="#fff" stroke-width="1.1"/><path d="M1 7 H13 M2 4 H12 M2 10 H12" stroke="#fff" stroke-width="1"/></svg>
        www.qvlegal.com.au
      </p>
    </div>
  </section>
</body>
</html>
```